Luxury Real Estate Website, Midwest, United States

We need web design services for a luxury website. We need IDX Integration with our MLS. We want this to be a very simple website with amazing graphics. We want it to link up with our MailNest account in order to generate leads through a "More Information" Pop up on the main page. We want the main page to be covered with one large graphic that is a rolling slideshow of active listings of $400,000 and up from the IDX Integration. We need this website to give a very exclusive and sleek look. Lots of black is good... I will upload our logos in Black and Silver. We will also need an "About" page that we are going to call "Qeno Info". We want our graphics to be extremely impressive. Keep in mind, we are a company in the Midwest of the United States, and our real estate has a different look than homes in California or Florida. We need graphics that are realistic for the Midwest, yet still high-end.
Target Market(s)
Luxury Homeowners in the Midwest United States. The graphics needs to be pristine.
Industry/Entity Type
Real Estate
Coding
Coded - Design and coding required
Number of Pages Required
3 page
Requirements
Must have
- Large graphics with IDX Integration. The photos of real estate need to represent real estate that is common in the Midwest, United States. We also need MailNest integration. We need a pop up that is titled "My Free Market Analysis" that makes them fill out a contact form asking for Full Name, Email Address, Phone Number and Address. This needs to be a pop up on the front page and will integrate with our MailNest account. We also need a page called "About Qe No Home". And another page where clients can download informational PDFs. The main component needs to be a front page search engine connected with the IDX to access active listings from our MLS. I attached our logos and a sample front page of a website. I would love for ours to look similar.
Nice to have
- Lake House photos on midwest lakes are a plus.
Should not have
- Should not have clutter. This website needs to be clean, luxurious and exclusive.

```html
<!DOCTYPE html>
<html lang="en">
<head>
<meta charset="utf-8">
<title>Hearthline Realty Group — Luxury Houses from Midwest</title>
<link href="https://fonts.googleapis.com/css2?family=Lato:wght@400;700;900&display=swap" rel="stylesheet">
<style>
:root{
  --ink:#1d1f23;
  --text:#4a4d52;
  --muted:#7c8187;
  --white:#ffffff;
  --band:#dfe4ea;
  --slate:#6d7e94;
  --slate-dark:#556579;
  --hero-sky:#9fb4c9;
  --hero-house:#b39a6a;
  --hero-lawn:#5d7a3c;
  --footer:#1c1d1f;
  --footer-line:#2e3033;
  --shade:rgba(0,0,0,.63);
}
*{box-sizing:border-box;margin:0;padding:0}
html,body{width:1200px;height:3696px;overflow:hidden}
body{position:relative;font-family:'Lato',Arial,sans-serif;color:var(--text);background:var(--white)}
.abs{position:absolute}

/* header */
.site-header{left:0;top:0;width:1200px;height:99px;background:var(--white);z-index:2}
.brand{left:99px;top:20px;display:flex;align-items:center;gap:12px}
.brand-mark{width:14px;height:14px;background:var(--ink)}
.brand-name{font-size:24px;font-weight:700;color:var(--ink);letter-spacing:1px;line-height:1}
.brand-sub{font-size:11px;letter-spacing:3px;color:var(--ink);margin-top:4px}
.account{top:14px;right:147px;display:flex;gap:12px}
.account a{display:block;height:36px;line-height:34px;padding:0 20px;border-radius:18px;font-size:12px;font-weight:700;text-decoration:none}
.btn-login{background:var(--ink);color:var(--white)}
.btn-signup{border:1px solid #b8bcc2;color:var(--muted)}
.main-nav{top:66px;right:99px;display:flex;gap:42px}
.main-nav a{font-size:13px;font-weight:700;color:var(--ink);text-decoration:none;letter-spacing:.5px}

/* hero */
.hero{left:0;top:99px;width:1200px;height:616px;overflow:hidden}
.hero-photo{width:100%;height:100%;background:linear-gradient(180deg,var(--hero-sky) 0%,#c9c3ad 30%,var(--hero-house) 48%,#7f7660 62%,var(--hero-lawn) 78%,#3f5a2c 100%)}
.hero-curve{left:0;bottom:0}
.hero-title{left:163px;top:201px;width:872px;height:60px;background:rgba(20,20,22,.82);color:var(--white);font-size:34px;font-weight:700;text-align:center;line-height:60px;letter-spacing:.5px}
.search{left:264px;top:315px;width:672px;height:54px;background:var(--white);border-radius:27px;display:flex;align-items:center;padding:0 18px;font-size:14px;color:var(--muted)}
.search-btn{position:absolute;right:8px;top:8px;width:38px;height:38px;border-radius:50%;background:#e6e8eb;display:flex;align-items:center;justify-content:center}

/* about */
.about-title{left:99px;top:822px;font-size:34px;font-weight:700;color:var(--ink)}
.about-lead{left:99px;top:878px;width:440px;font-size:16px;font-weight:700;color:var(--text);line-height:1.5}
.about-body{left:99px;top:960px;width:460px;font-size:12.5px;line-height:1.75;color:var(--muted)}
.btn-slate{display:block;height:42px;line-height:42px;padding:0 24px;border-radius:21px;background:var(--slate);color:var(--white);font-size:12px;font-weight:700;text-decoration:none}
.about-more{left:99px;top:1140px}
.about-plate{left:567px;top:833px;width:532px;height:315px;background:var(--band)}
.about-photo{left:601px;top:875px;width:459px;height:313px;background:linear-gradient(180deg,#a9b8c7 0%,#d8d2c6 45%,#f2efe9 70%,#9a7e6a 100%)}

/* features band */
.features{left:0;top:1318px;width:1200px;height:427px;background:var(--band)}
.features-photo{left:99px;top:1284px;width:475px;height:374px;background:linear-gradient(135deg,#3b3129 0%,#7a5c44 45%,#b38e6c 70%,#4a3c31 100%)}
.features-caption{left:187px;top:1562px;width:217px;height:205px;background:var(--slate);padding:22px 20px;color:var(--white)}
.features-caption h4{font-size:20px;line-height:1.3;font-weight:400;color:#e8ecf1}
.features-caption p{font-size:11px;line-height:1.6;margin-top:10px;color:#cdd5df}
.dots{display:flex;gap:8px}
.dots i{display:block;width:9px;height:9px;border-radius:50%;background:#c5ccd6}
.dots i.on{background:var(--white)}
.caption-dots{position:absolute;left:20px;bottom:18px}
.feature{left:631px;width:470px}
.feature h3{font-size:22px;font-weight:700;color:var(--ink)}
.feature p{margin-top:10px;font-size:12.5px;line-height:1.7;color:var(--muted)}
.feature a{display:inline-block;margin-top:10px;font-size:12px;font-weight:700;color:var(--ink);text-decoration:none}

/* popular */
.section-title{left:0;width:1200px;text-align:center;font-size:30px;font-weight:700;color:var(--ink)}
.section-sub{left:0;width:1200px;text-align:center;font-size:12px;color:var(--muted)}
.card{top:1929px;width:320px;height:355px;background:var(--white);border:1px solid #e4e6e9}
.card-photo{height:246px}
.card h5{margin:18px 18px 0;font-size:15px;font-weight:700;color:var(--ink)}
.card .loc{display:flex;gap:8px;margin:8px 18px 0;font-size:11.5px;line-height:1.5;color:var(--muted)}
.pager{left:526px;top:2324px;display:flex;gap:14px}
.pager i{display:block;width:44px;height:5px;background:#c9d0d9}
.pager i.on{background:var(--slate)}

/* cta */
.cta{left:0;top:2427px;width:1200px;height:333px;background:linear-gradient(180deg,#4c4f4c 0%,#6a6c62 45%,#3d4a32 100%)}
.cta h2{position:absolute;top:70px;width:100%;text-align:center;font-size:34px;font-weight:700;color:var(--white)}
.cta p{position:absolute;top:130px;left:300px;width:600px;text-align:center;font-size:13px;line-height:1.7;color:#e2e4e6}
.cta-actions{position:absolute;top:208px;left:0;width:100%;display:flex;justify-content:center;gap:18px}
.cta-actions a{height:42px;line-height:40px;padding:0 30px;border-radius:21px;font-size:13px;font-weight:700;color:var(--white);text-decoration:none}
.btn-fill{background:var(--slate);border:1px solid var(--slate)}
.btn-ghost{border:1px solid var(--white)}

/* testimonial + partners */
.col-title{top:2846px;font-size:26px;font-weight:700;color:var(--ink)}
.testimonial{left:99px;top:2927px;width:485px;height:210px;border:1px solid #dcdfe3;padding:30px 24px;background:var(--white)}
.testimonial p{width:380px;font-size:11.5px;line-height:1.7;color:var(--muted)}
.quote-badge{position:absolute;right:24px;top:-20px;width:52px;height:52px;border-radius:50%;background:var(--slate);display:flex;align-items:center;justify-content:center}
.person{position:absolute;left:24px;bottom:30px}
.person b{font-size:16px;color:var(--ink)}
.person span{font-size:11px;color:var(--muted);margin-left:6px}
.stars{display:flex;gap:3px;margin-top:8px}
.avatar{position:absolute;right:24px;bottom:24px;width:72px;height:72px;border-radius:50%;background:linear-gradient(135deg,#c8b8a6,#8a7664)}
.arrows{left:526px;top:3152px;display:flex;gap:12px}
.arrows span{width:26px;height:26px;border-radius:50%;background:var(--ink);display:flex;align-items:center;justify-content:center}
.partners{left:621px;top:2908px;width:478px;height:202px;display:grid;grid-template-columns:repeat(3,1fr);grid-template-rows:repeat(2,1fr)}
.partners div{display:flex;align-items:center;justify-content:center;border-right:1px solid #e3e5e8;border-bottom:1px solid #e3e5e8}
.partners div:nth-child(3n){border-right:none}
.partners div:nth-child(n+4){border-bottom:none}
.partner-badge{width:110px;height:44px;background:#c9d2dc;border-radius:4px}

/* footer */
.site-footer{left:0;top:3272px;width:1200px;height:424px;background:var(--footer)}
.f-col{top:86px}
.f-col h6{font-size:17px;font-weight:700;color:var(--white);margin-bottom:24px;letter-spacing:.3px}
.f-links li{list-style:none;font-size:12px;color:#9a9ea3;line-height:2}
.f-contact li{list-style:none;display:flex;gap:12px;font-size:11.5px;color:#9a9ea3;line-height:1.6;margin-bottom:26px;width:250px}
.f-input{width:260px;height:38px;background:#f2f2f2;padding:0 12px;line-height:38px;font-size:12px;color:var(--muted)}
.f-sub{margin-top:14px;width:134px;height:38px;background:#2b2c2f;line-height:38px;text-align:center;font-size:12px;font-weight:700;color:var(--white)}
.f-social li{list-style:none;display:flex;align-items:center;gap:14px;font-size:12px;color:#9a9ea3;margin-bottom:14px}
.f-social i{display:block;width:30px;height:30px;border-radius:50%}
.copyright{left:0;top:380px;width:1200px;border-top:1px solid var(--footer-line);padding-top:14px;text-align:center;font-size:11px;color:#6f7378}
.side-tab{right:0;top:3363px;width:57px;height:210px;background:var(--white);border-radius:14px 0 0 14px;display:flex;flex-direction:column;align-items:center;padding-top:18px;gap:16px}
.side-tab span{writing-mode:vertical-rl;transform:rotate(180deg);font-size:11px;font-weight:700;color:var(--ink);letter-spacing:1px}

/* overlay + popup */
.shade{left:0;top:0;width:1200px;height:3696px;background:var(--shade);z-index:10}
.popup{left:362px;top:476px;width:478px;height:404px;background:var(--white);z-index:11;padding:40px 45px}
.popup h2{text-align:center;font-size:17px;font-weight:900;color:var(--ink);letter-spacing:.3px}
.popup-close{position:absolute;right:16px;top:12px;width:26px;height:26px;border-radius:50%;background:var(--ink);display:flex;align-items:center;justify-content:center}
.field{margin-top:20px;height:38px;border:1px solid #c9ccd0;padding:0 10px;line-height:36px;font-size:12px;color:var(--ink)}
.field:first-of-type{margin-top:34px}
.popup-foot{display:flex;align-items:center;gap:20px;margin-top:26px}
.btn-send{width:98px;height:36px;border-radius:18px;background:#0c0c0d;color:var(--white);font-size:13px;font-weight:700;text-align:center;line-height:36px}
.partner-mail{display:flex;align-items:center;gap:8px;font-size:16px;font-weight:700;color:var(--ink)}
.partner-mail i{display:block;width:24px;height:24px;border-radius:50%;background:#e8e9eb}
</style>
</head>
<body>

<header class="site-header abs">
  <div class="brand abs">
    <span class="brand-mark"></span>
    <div>
      <div class="brand-name">HEARTHLINE</div>
      <div class="brand-sub">REALTY GROUP</div>
    </div>
  </div>
  <div class="account abs">
    <a class="btn-login" href="#">LOGIN</a>
    <a class="btn-signup" href="#">SIGNUP</a>
  </div>
  <nav class="main-nav abs">
    <a href="#">HOME</a><a href="#">QENO INFO</a><a href="#">ABOUT QE NO HOME</a><a href="#">DOWNLOADS</a><a href="#">CONTACT US</a>
  </nav>
</header>

<section class="hero abs">
  <div class="hero-photo" role="img" aria-label="Large Midwest luxury home with lawn, trees and fountain"></div>
  <svg class="hero-curve abs" width="1200" height="90" viewBox="0 0 1200 90"><path d="M0 90 L0 40 Q600 -20 1200 40 L1200 90 Z" fill="#ffffff"/><path d="M0 40 Q600 -20 1200 40" fill="none" stroke="#6d7e94" stroke-width="8" opacity=".7"/></svg>
  <h1 class="hero-title abs">LUXURY HOUSES FROM MIDWEST, UNITED STATES</h1>
  <div class="search abs">Search homes by city &amp; state,zip, or MLS#
    <span class="search-btn"><svg width="16" height="16" viewBox="0 0 16 16"><circle cx="7" cy="7" r="5" fill="none" stroke="#1d1f23" stroke-width="2"/><path d="M11 11l4 4" stroke="#1d1f23" stroke-width="2"/></svg></span>
  </div>
</section>

<section>
  <div class="about-plate abs"></div>
  <div class="about-photo abs" role="img" aria-label="Bright living room with white sofa and lake view"></div>
  <h2 class="about-title abs">About Qe No Home</h2>
  <p class="about-lead abs">Sed ut perspiciatis unde omnis iste natus error sit voluptatem accusantium doloremque laudantium</p>
  <p class="about-body abs">Lorem ipsum dolor sit amet, consectetur adipiscing elit, sed do eiusmod tempor incididunt ut labore et dolore magna aliqua. Ut enim ad minim veniam, quis nostrud exercitation ullamco laboris nisi ut aliquip ex ea commodo consequat. Duis aute irure dolor in reprehenderit in voluptate velit esse cillum dolore eu fugiat nulla pariatur. Excepteur sint occaecat cupidatat non proident, sunt in culpa qui officia deserunt mollit anim id est laborum.</p>
  <a class="btn-slate about-more abs" href="#">LEARN MORE &gt;&gt;</a>
</section>

<section>
  <div class="features abs"></div>
  <div class="features-photo abs" role="img" aria-label="Agents meeting with a family in a cozy home"></div>
  <div class="features-caption abs">
    <h4>Nemo enim ipsam voluptatem dolor voluptas sit</h4>
    <p>sed quia non numquam eius modi tempora incidunt</p>
    <div class="dots caption-dots"><i class="on"></i><i></i><i></i></div>
  </div>
  <div class="feature abs" style="top:1373px">
    <h3>Customer Satisfaction</h3>
    <p>Lorem ipsum dolor sit amet, consectetur adipiscing elit, sed do eiusmod tempor incididunt ut labore et dolore magna aliqua. Ut enim ad minim veniam, quis nostrud exercitation ullamco laboris nisi ut aliquip.</p>
    <a href="#">Learn More &gt;&gt;</a>
  </div>
  <div class="feature abs" style="top:1537px">
    <h3>Best Service Certification</h3>
    <p>Lorem ipsum dolor sit amet, consectetur adipiscing elit, sed do eiusmod tempor incididunt ut labore et dolore magna aliqua. Ut enim ad minim veniam, quis nostrud exercitation ullamco laboris nisi ut aliquip.</p>
    <a href="#">Learn More &gt;&gt;</a>
  </div>
</section>

<section>
  <h2 class="section-title abs" style="top:1820px">Most Popular Places</h2>
  <p class="section-sub abs" style="top:1872px">Lorem ipsum dolor sit amet, consectetur adipiscing elit, sed do eiusmod tempor</p>
  <article class="card abs" style="left:99px">
    <div class="card-photo" role="img" aria-label="White lakeside mansion among trees" style="background:linear-gradient(180deg,#6b7f5c,#e9ece8 50%,#4d6a3a)"></div>
    <h5>Labore et dolore magna aliqua. Ut enim</h5>
    <div class="loc"><svg width="10" height="14" viewBox="0 0 10 14"><path d="M5 0a5 5 0 0 1 5 5c0 4-5 9-5 9S0 9 0 5a5 5 0 0 1 5-5z" fill="#1d1f23"/><circle cx="5" cy="5" r="2" fill="#fff"/></svg><span>Error sit voluptatem accusantium doloremque laudantium, totam rem aperiam, eaque ipsa</span></div>
  </article>
  <article class="card abs" style="left:439px">
    <div class="card-photo" role="img" aria-label="Pool terrace framed by curtains" style="background:linear-gradient(180deg,#d8d0c2,#7fb3c9 60%,#c9b89d)"></div>
    <h5>Labore et dolore magna aliqua. Ut enim</h5>
    <div class="loc"><svg width="10" height="14" viewBox="0 0 10 14"><path d="M5 0a5 5 0 0 1 5 5c0 4-5 9-5 9S0 9 0 5a5 5 0 0 1 5-5z" fill="#1d1f23"/><circle cx="5" cy="5" r="2" fill="#fff"/></svg><span>Error sit voluptatem accusantium doloremque laudantium, totam rem aperiam, eaque ipsa</span></div>
  </article>
  <article class="card abs" style="left:779px">
    <div class="card-photo" role="img" aria-label="Modern lounge with lake view windows" style="background:linear-gradient(180deg,#2e2f31,#9fb2c2 45%,#8d4b48 80%,#3c3d3f)"></div>
    <h5>Labore et dolore magna aliqua. Ut enim</h5>
    <div class="loc"><svg width="10" height="14" viewBox="0 0 10 14"><path d="M5 0a5 5 0 0 1 5 5c0 4-5 9-5 9S0 9 0 5a5 5 0 0 1 5-5z" fill="#1d1f23"/><circle cx="5" cy="5" r="2" fill="#fff"/></svg><span>Error sit voluptatem accusantium doloremque laudantium, totam rem aperiam, eaque ipsa</span></div>
  </article>
  <div class="pager abs"><i class="on"></i><i></i><i class="on"></i></div>
</section>

<section class="cta abs" role="img" aria-label="Evening view of a large family home">
  <h2>Looking for best home ever!</h2>
  <p>Sed ut perspiciatis unde omnis iste natus error sit voluptatem accusantium doloremque laudantium, totam rem aperiam. Nemo enim ipsam voluptatem quia voluptas sit aspernatur aut odit aut fugit.</p>
  <div class="cta-actions"><a class="btn-fill" href="#">Purchase Now</a><a class="btn-ghost" href="#">View More Info</a></div>
</section>

<section>
  <h2 class="col-title abs" style="left:99px">Testimonial</h2>
  <h2 class="col-title abs" style="left:631px">Our Partners</h2>
  <div class="testimonial abs">
    <span class="quote-badge"><svg width="20" height="16" viewBox="0 0 20 16"><path d="M0 16V9C0 4 3 1 8 0v3C5 4 4 6 4 8h4v8zM12 16V9c0-5 3-8 8-9v3c-3 1-4 3-4 5h4v8z" fill="#fff"/></svg></span>
    <p>Sed ut perspiciatis unde omnis iste natus error sit voluptatem accusantium doloremque laudantium, totam rem aperiam, eaque ipsa quae ab illo inventore veritatis et quasi architecto beatae vitae dicta sunt explicabo. Nemo enim ipsam voluptatem quia voluptas sit aspernatur.</p>
    <div class="person"><b>Sit voluptatem</b><span>City Location</span>
      <div class="stars">
        <svg width="13" height="13" viewBox="0 0 10 10"><path d="M5 0l1.5 3.2 3.5.4-2.6 2.4.7 3.5L5 7.8 1.9 9.5l.7-3.5L0 3.6l3.5-.4z" fill="#d9a21b"/></svg>
        <svg width="13" height="13" viewBox="0 0 10 10"><path d="M5 0l1.5 3.2 3.5.4-2.6 2.4.7 3.5L5 7.8 1.9 9.5l.7-3.5L0 3.6l3.5-.4z" fill="#d9a21b"/></svg>
        <svg width="13" height="13" viewBox="0 0 10 10"><path d="M5 0l1.5 3.2 3.5.4-2.6 2.4.7 3.5L5 7.8 1.9 9.5l.7-3.5L0 3.6l3.5-.4z" fill="#d9a21b"/></svg>
        <svg width="13" height="13" viewBox="0 0 10 10"><path d="M5 0l1.5 3.2 3.5.4-2.6 2.4.7 3.5L5 7.8 1.9 9.5l.7-3.5L0 3.6l3.5-.4z" fill="#d9a21b"/></svg>
        <svg width="13" height="13" viewBox="0 0 10 10"><path d="M5 0l1.5 3.2 3.5.4-2.6 2.4.7 3.5L5 7.8 1.9 9.5l.7-3.5L0 3.6l3.5-.4z" fill="#d9a21b"/></svg>
      </div>
    </div>
    <div class="avatar" role="img" aria-label="Client portrait"></div>
  </div>
  <div class="arrows abs">
    <span><svg width="10" height="10" viewBox="0 0 10 10"><path d="M7 1L3 5l4 4" stroke="#fff" stroke-width="2" fill="none"/></svg></span>
    <span><svg width="10" height="10" viewBox="0 0 10 10"><path d="M3 1l4 4-4 4" stroke="#fff" stroke-width="2" fill="none"/></svg></span>
  </div>
  <div class="partners abs">
    <div><span class="partner-badge"></span></div><div><span class="partner-badge"></span></div><div><span class="partner-badge"></span></div>
    <div><span class="partner-badge"></span></div><div><span class="partner-badge"></span></div><div><span class="partner-badge"></span></div>
  </div>
</section>

<footer class="site-footer abs">
  <div class="f-col abs" style="left:99px"><h6>QUICK LINKS</h6>
    <ul class="f-links"><li>Home</li><li>Qeno Info</li><li>About Qe No Home</li><li>Downloads</li><li>Contact us</li></ul>
  </div>
  <div class="f-col abs" style="left:313px"><h6>CONTACT US</h6>
    <ul class="f-contact">
      <li><svg width="12" height="16" viewBox="0 0 10 14"><path d="M5 0a5 5 0 0 1 5 5c0 4-5 9-5 9S0 9 0 5a5 5 0 0 1 5-5z" fill="#9a9ea3"/></svg><span>418 Birchwood Lane, Suite 12<br>Maple Ridge, Ohio</span></li>
      <li><svg width="14" height="14" viewBox="0 0 14 14"><path d="M3 0l3 3-2 2c1 2 3 4 5 5l2-2 3 3-2 3C6 14 0 8 0 2z" fill="#9a9ea3"/></svg><span>(555) 014-2736</span></li>
      <li><svg width="14" height="12" viewBox="0 0 14 12"><rect width="14" height="12" rx="1" fill="#9a9ea3"/><path d="M0 1l7 5 7-5" stroke="#1c1d1f" fill="none"/></svg><span>hello@hearthlinerealty.com</span></li>
    </ul>
  </div>
  <div class="f-col abs" style="left:626px"><h6>NEWSLETTER</h6>
    <div class="f-input">Email ID</div><div class="f-sub">SUBSCRIBE</div>
  </div>
  <div class="f-col abs" style="left:978px"><h6>FOLLOW US</h6>
    <ul class="f-social">
      <li><i style="background:#3b5a9a"></i>Facepage</li>
      <li><i style="background:#2fa7df"></i>Chirper</li>
      <li><i style="background:#d9482f"></i>Globe Plus</li>
      <li><i style="background:#c4302b"></i>ViewTube</li>
    </ul>
  </div>
  <div class="copyright abs">Copyright © 2016 Hearthline Realty Group . All Rights Reserved</div>
</footer>
<div class="side-tab abs">
  <svg width="14" height="14" viewBox="0 0 14 14"><path d="M3 0l3 3-2 2c1 2 3 4 5 5l2-2 3 3-2 3C6 14 0 8 0 2z" fill="#1d1f23"/></svg>
  <span>GET TO KNOW US</span>
</div>

<div class="shade abs"></div>
<form class="popup abs">
  <span class="popup-close"><svg width="10" height="10" viewBox="0 0 10 10"><path d="M1 1l8 8M9 1l-8 8" stroke="#fff" stroke-width="2"/></svg></span>
  <h2>MY FREE MARKET ANALYSIS</h2>
  <div class="field">Full Name</div>
  <div class="field">Email Address</div>
  <div class="field">Phone Number</div>
  <div class="field">Address</div>
  <div class="popup-foot"><span class="btn-send">SEND</span><span class="partner-mail"><i></i>MailNest</span></div>
</form>

</body>
</html>
```